Vibrant, yet professional, stationery set and other designs required.

I need to source a fantastic designer for a new project as part of my company using a new logo designed via sketch harbor.

**UPDATE** I am not looking for just 'fine' design that will suffice. I am looking for something great.

We are a life assurance brokerage based in Dublin, Ireland and BrightRoost.ie is our new website aimed at providing services for young families in Ireland. We are hoping to be the 'Velro' level of service providers in this area and I am looking for the quality of design to reflect this :-) Hopefully that makes sense!

I have a preference for straight lines over curves and waves.

I need...

1. Business card
2. Letterhead
3. Banner (for printing - 76cm X 305cm)
4. Car branding for KORVA 9 (2014 sport model) I believe the templates are freely available online.

Target Market(s)

Parents in Ireland - Aged 27 to 50.

Industry/Entity Type

Financial Planning

Colors

Designer to choose colors to be used in the design.

Requirements
Must have
• All of the items listed in the description above. I like clean, bright, legible, vibrant and professional design.
Should not have
• No silly or 'cheap' looking designs. This is a professional company looking to provide a professional service.

```html
<!DOCTYPE html>
<html lang="en">
<head>
<meta charset="utf-8">
<title>BrightRoost.ie – Business Card</title>
<link rel="stylesheet" href="https://fonts.googleapis.com/css2?family=Oswald:wght@500&family=Roboto:wght@400;500&display=swap">
<style>
  :root {
    --backdrop: #2e2f31;
    --card-front: #f7f8f8;
    --card-back: #9ba6a8;
    --card-back-light: #a7b1b3;
    --brand-grey: #7b8689;
    --brand-orange: #f07c1f;
    --ink-light: #ffffff;
  }
  * { margin: 0; padding: 0; box-sizing: border-box; }
  html, body { width: 1200px; height: 900px; overflow: hidden; }
  body {
    background: var(--backdrop);
    font-family: "Roboto", Arial, sans-serif;
    position: relative;
  }
  .card {
    position: absolute;
    left: 300px;
    width: 600px;
    height: 340px;
    box-shadow: 0 10px 30px rgba(0,0,0,.35);
  }
  .card--front {
    top: 90px;
    background: var(--card-front);
    display: flex;
    align-items: center;
    justify-content: center;
  }
  .brand {
    display: flex;
    align-items: center;
    gap: 14px;
    color: var(--brand-grey);
    font-family: "Roboto", Arial, sans-serif;
    font-weight: 500;
    font-size: 58px;
    letter-spacing: -1px;
  }
  .brand__dot {
    width: 22px; height: 22px;
    border-radius: 50%;
    background: var(--brand-orange);
  }
  .card--back {
    top: 470px;
    background: linear-gradient(100deg, var(--card-back) 0%, var(--card-back-light) 100%);
    color: var(--ink-light);
  }
  .identity {
    position: absolute;
    right: 330px;
    top: 118px;
    text-align: right;
  }
  .identity__name {
    font-family: "Oswald", "Arial Narrow", sans-serif;
    font-weight: 500;
    font-size: 34px;
    letter-spacing: .5px;
    line-height: 1;
  }
  .identity__role {
    margin-top: 8px;
    font-size: 15px;
    font-weight: 500;
    letter-spacing: .5px;
  }
  .divider {
    position: absolute;
    left: 288px;
    top: 108px;
    width: 2px;
    height: 110px;
    background: var(--ink-light);
  }
  .contacts {
    position: absolute;
    left: 308px;
    top: 108px;
    list-style: none;
    font-size: 15px;
  }
  .contacts li {
    display: flex;
    align-items: center;
    gap: 10px;
    height: 22px;
  }
  .contacts svg { width: 14px; height: 14px; fill: var(--ink-light); flex: none; }
  .address {
    position: absolute;
    left: 92px;
    top: 272px;
    display: flex;
    align-items: center;
    gap: 10px;
    font-size: 16px;
  }
  .address svg { width: 14px; height: 18px; fill: var(--ink-light); }
</style>
</head>
<body>
  <section class="card card--front">
    <div class="brand">
      <span class="brand__dot"></span>
      <span class="brand__name">BrightRoost.ie</span>
    </div>
  </section>

  <section class="card card--back">
    <div class="identity">
      <p class="identity__name">LIAM CARROWAY</p>
      <p class="identity__role">CEO/FOUNDER</p>
    </div>
    <div class="divider"></div>
    <ul class="contacts">
      <li>
        <svg viewBox="0 0 14 14" aria-hidden="true"><path d="M3 0.5 5.2 3 4 4.6c.9 2 2.4 3.5 4.4 4.4L10 7.8l2.5 2.2-1.2 2.8C6 12.5 1.5 8 1.2 2.7Z"/></svg>
        <span>614 205 7731</span>
      </li>
      <li>
        <svg viewBox="0 0 14 14" aria-hidden="true"><path d="M3.5 0h7v14h-7Zm1.3 1.5v9.5h4.4V1.5Z"/></svg>
        <span>872 319 4406</span>
      </li>
      <li>
        <svg viewBox="0 0 14 14" aria-hidden="true"><path d="M3.5 0h7v4h-7ZM0 5h14v6h-2.5v3h-9v-3H0Zm4.5 5v2.5h5V10Z"/></svg>
        <span>455 760 2189</span>
      </li>
      <li>
        <svg viewBox="0 0 14 14" aria-hidden="true"><path d="M0 3h14v1L7 8.5 0 4Zm0 2.5 7 4.5 7-4.5V11H0Z"/></svg>
        <span>liam@brightroost.com</span>
      </li>
      <li>
        <svg viewBox="0 0 14 14" aria-hidden="true"><path d="M7 0a7 7 0 1 0 0 14A7 7 0 0 0 7 0Zm0 1.5a5.5 5.5 0 0 1 5.5 5.5H1.5A5.5 5.5 0 0 1 7 1.5Z"/></svg>
        <span>www.brightroost.com</span>
      </li>
    </ul>
    <p class="address">
      <svg viewBox="0 0 14 18" aria-hidden="true"><path d="M7 0a7 7 0 0 0-7 7c0 5 7 11 7 11s7-6 7-11a7 7 0 0 0-7-7Zm0 4a3 3 0 1 1 0 6 3 3 0 0 1 0-6Z"/></svg>
      <span>14 Larkfield Row, Rathmines, Dublin D06 K2X4</span>
    </p>
  </section>
</body>
</html>
```